Menu Design Project

Menu design for a Japanese fast food restaurant featuring Teppanyaki and Sushi. The restaurant main scene color is black and wood color. No Japan scenery pictures. Menu try to be simply and elegant . Pictures provided can be used accordingly to the menu items, but doesn't have to be due to the back ground color of the picture is white.

Target Market(s)

Young and progressive consumers

Industry/Entity Type

Asian Restaurant

Font styles to use
Other font styles liked:
• Han Wang Kan Tan Font

Colors
1b1b1b
fee18a

Requirements
Must have
• Pictures of the Sushi that is provided, and all the item in the Word file.
Nice to have
• Keep it simple but different
Should not have
• No scenery pictures, no cherry blossom.

```html
<!DOCTYPE html>
<html lang="en">
<head>
<meta charset="utf-8">
<title>Teppanyaki &amp; Sushi Menu</title>
<link rel="stylesheet" href="https://fonts.googleapis.com/css2?family=Lilita+One&family=Open+Sans:wght@400;600;700&display=swap">
<style>
  :root{
    --page-bg:#f1ede6;
    --wood-light:#f0e0c2;
    --wood-mid:#e6cfa6;
    --band-soft:rgba(214,151,74,.55);
    --ink:#2b1f14;
    --ink-soft:#5a4631;
    --brush:#9c7640;
    --gold:#fee18a;
    --charcoal:#1b1b1b;
    --calligraphy-tone:#c9a777;
    --photo-frame:#ffffff;
  }
  *{box-sizing:border-box;margin:0;padding:0}
  html,body{width:1200px;height:863px;overflow:hidden}
  body{background:var(--page-bg);font-family:"Open Sans",sans-serif;color:var(--ink);position:relative}
  .spread{position:absolute;left:36px;top:96px;display:flex;box-shadow:0 6px 18px rgba(0,0,0,.18)}
  .panel{width:272px;height:672px;padding:18px 16px;background:linear-gradient(170deg,var(--wood-light) 0%,var(--wood-mid) 55%,var(--wood-light) 100%);border-right:1px solid rgba(120,90,50,.25);display:flex;flex-direction:column;gap:7px}
  .panel:last-child{border-right:none}
  .section-title{align-self:center;font-family:"Lilita One",sans-serif;font-size:22px;color:var(--gold);text-shadow:0 1px 0 var(--charcoal);padding:0 26px;background:linear-gradient(90deg,transparent,var(--brush) 15%,var(--brush) 85%,transparent);letter-spacing:.5px}
  .section-note{text-align:center;font-size:9px;color:var(--ink-soft);line-height:1.25}
  .price-list{list-style:none;font-size:9.5px;line-height:12.4px;padding:0 6px}
  .price-list li{display:flex;justify-content:space-between}
  .price-list .price{font-weight:700}
  .sub-title{font-weight:700;font-size:12px;margin-top:2px}
  .item{position:relative;background:linear-gradient(90deg,var(--band-soft),rgba(214,151,74,.15));padding:5px 8px;min-height:40px;font-size:8.5px;line-height:1.3;color:var(--ink-soft)}
  .item.has-photo{padding-right:78px}
  .item.left-photo{padding-left:78px;padding-right:8px}
  .item-name{display:block;font-weight:700;font-size:10px;color:var(--ink)}
  .item .price{font-weight:700;color:var(--ink)}
  .photo{position:absolute;top:50%;transform:translateY(-50%);right:6px;width:66px;height:46px;border:3px solid var(--photo-frame);box-shadow:0 1px 3px rgba(0,0,0,.25);background:linear-gradient(120deg,#f6f1e6 0%,#f08a5a 40%,#93b46a 70%,#f6f1e6 100%)}
  .left-photo .photo{left:6px;right:auto}
  .photo.dark{background:radial-gradient(circle,#f06d55 20%,#f5f0e6 45%,#222 70%)}
  .photo.tempura{background:linear-gradient(120deg,#fff 10%,#e9b25a 50%,#fff 90%)}
  .cover{position:absolute;left:880px;top:96px;width:272px;height:672px;background:linear-gradient(170deg,var(--wood-light),var(--wood-mid));box-shadow:0 6px 18px rgba(0,0,0,.18);overflow:hidden}
  .cover-inner{position:absolute;left:26px;right:0;top:96px;bottom:0;background:#f7f1e4}
  .cover-calligraphy{position:absolute;left:46px;top:50px;width:140px;height:150px;background:radial-gradient(ellipse at center,var(--calligraphy-tone) 0%,rgba(201,167,119,.45) 55%,rgba(201,167,119,0) 80%)}
  .cover-photo{position:absolute;left:26px;right:0;top:270px;bottom:0;background:radial-gradient(ellipse at 45% 55%,#c9845e 0%,#e1a57a 18%,#b6c777 30%,#faf6ee 48%,#f3ead8 70%,#d07a3c 100%)}
</style>
</head>
<body>
  <main class="spread">
    <section class="panel panel-entree">
      <h2 class="section-title">Entree</h2>
      <p class="section-note">with Hibachi Vegetable and Fried Rice, or<br>Yakisoba Noodle add 0.99</p>
      <ul class="price-list">
        <li><span>Teriyaki Chicken</span><span class="price">6.89</span></li>
        <li><span>(double Chicken Special 1.59)</span><span class="price">7.29</span></li>
        <li><span>Teriyaki Beef</span><span class="price">7.89</span></li>
        <li><span>Teriyaki Shrimp</span><span class="price">8.89</span></li>
        <li><span>Teriyaki Chicken &amp; Shrimp</span><span class="price">8.49</span></li>
        <li><span>Teriyaki Chicken &amp; Beef</span><span class="price">9.29</span></li>
        <li><span>Teriyaki Beef &amp; Shrimp</span><span class="price">10.29</span></li>
        <li><span>Teriyaki Chicken Beef &amp; Shrimp</span><span class="price">7.59</span></li>
        <li><span>Hibachi Chicken</span><span class="price">7.99</span></li>
        <li><span>Hibachi Beef</span><span class="price">8.59</span></li>
        <li><span>Hibachi Shrimp</span><span class="price">9.59</span></li>
        <li><span>Hibachi Chicken &amp; Shrimp</span><span class="price">9.19</span></li>
        <li><span>Hibachi Chicken &amp; Beef</span><span class="price">9.99</span></li>
        <li><span>Hibachi Beef &amp; Shrimp</span><span class="price">10.99</span></li>
        <li><span>Hibachi Chicken, Beef &amp; Shrimp</span><span class="price">11.49</span></li>
      </ul>
      <h2 class="section-title">Sushi</h2>
      <p class="section-note">Ingredients subject to availability</p>
      <h3 class="sub-title">Special Roll</h3>
      <div class="item has-photo"><span class="item-name">Dragon Roll</span>Grilled Eel fish &amp; cucumber top with avocado &amp; Unagi sauce <span class="price">9.99</span><div class="photo" role="img" aria-label="Photo of dragon roll"></div></div>
      <div class="item"><span class="item-name">Deluxe Black Dragon Roll</span>Tempura Shrimp top with Avocado, Grilled Eel fish &amp; Unagi sauce <span class="price">11.99</span></div>
      <div class="item left-photo"><span class="item-name">*Rainbow Roll</span>avocado, cucumber &amp; Kani top with red snapper, tuna, salmon &amp; avocado <span class="price">10.99</span><div class="photo" role="img" aria-label="Photo of rainbow roll"></div></div>
      <div class="item"><span class="item-name">*Four Season Roll</span>Tuna, salmon, oshinko <span class="price">9.99</span></div>
      <div class="item"><span class="item-name">*Deluxe Philly Roll</span>Salmon, cream cheese &amp; avocado top with more salmon <span class="price">9.99</span></div>
    </section>

    <section class="panel panel-special">
      <div class="item left-photo"><span class="item-name">*Massago Roll</span>Kani crab meat, cucumber &amp; avocado top with Premium Massago Roe <span class="price">8.99</span><div class="photo" role="img" aria-label="Photo of massago roll"></div></div>
      <div class="item"><span class="item-name">*Deluxe Spicy Tuna Roll</span>Kani crab meat, cucumber &amp; avocado top with spicy grounded tuna <span class="price">9.49</span></div>
      <div class="item left-photo"><span class="item-name">Deluxe Spicy Kani Roll</span>Kani crab meat, cucumber &amp; avocado top with seasoned ground Crab meat <span class="price">9.49</span><div class="photo" role="img" aria-label="Photo of deluxe spicy kani roll"></div></div>
      <div class="item"><span class="item-name">Deluxe Kani Roll</span>Kani crab meat, cucumber &amp; avocado top with Kani &amp; Panko crumb <span class="price">9.49</span></div>
      <div class="item left-photo"><span class="item-name">*Tri Deluxe Fish Roll</span>Tuna, salmon &amp; red snapper <span class="price">9.99</span><div class="photo dark" role="img" aria-label="Photo of tri deluxe fish roll"></div></div>
      <div class="item"><span class="item-name">*Sumo Roll Tuna</span>Salmon, White Tuna, Red snapper Avocado &amp; Kani Crab Meat <span class="price">10.99</span></div>
      <div class="item"><span class="item-name">*Hamachi Asparagus Roll</span>Hamachi, Scallion &amp; Asparagus with Ponzu Sauce <span class="price">7.99</span></div>
      <h3 class="sub-title">Regular Maki Roll</h3>
      <div class="item has-photo"><span class="item-name">*Salmon Roll</span>salmon &amp; avocado (8pcs) <span class="price">5.49</span> (12pcs) <span class="price">7.49</span><div class="photo dark" role="img" aria-label="Photo of salmon roll"></div></div>
      <div class="item left-photo"><span class="item-name">*Tuna Roll</span>tuna &amp; avocado (8pcs) <span class="price">5.49</span> (12pcs) <span class="price">7.49</span><div class="photo dark" role="img" aria-label="Photo of tuna roll"></div></div>
    </section>

    <section class="panel panel-maki">
      <div class="item"><span class="item-name">*Philly Roll</span>salmon, cream cheese &amp; avocado (8pcs) <span class="price">5.49</span> (12pcs) <span class="price">7.49</span></div>
      <div class="item"><span class="item-name">California Roll</span>cucumber, avocado &amp; kani crab meat (8pcs) <span class="price">5.49</span> (12pcs) <span class="price">7.49</span></div>
      <div class="item"><span class="item-name">Kani &amp; Cheese Roll</span>Kani crab meat &amp; cream cheese (8pcs) <span class="price">5.49</span> (12pcs) <span class="price">7.49</span></div>
      <div class="item left-photo"><span class="item-name">Shrimp Tempura Roll</span>Fried tempura shrimp &amp; cucumber (8pcs) <span class="price">6.49</span><div class="photo tempura" role="img" aria-label="Photo of shrimp tempura roll"></div></div>
      <div class="item"><span class="item-name">*Alaska Roll</span>Salmon &amp; avocado with massago (8pcs) <span class="price">5.49</span> (12pcs) <span class="price">7.49</span></div>
      <div class="item left-photo"><span class="item-name">Grilled Eel Roll</span>Eel &amp; avocado (8pcs) <span class="price">5.49</span> (12pcs) <span class="price">7.49</span><div class="photo" role="img" aria-label="Photo of grilled eel hand roll"></div></div>
      <div class="item"><span class="item-name">*Spicy Tuna Roll</span>seasoned ground tuna (8pcs) <span class="price">5.49</span> (12pcs) <span class="price">7.49</span></div>
      <div class="item"><span class="item-name">*Spicy Salmon Roll</span>seasoned ground salmon (8pcs) <span class="price">5.49</span> (12pcs) <span class="price">7.49</span></div>
      <div class="item"><span class="item-name">Spicy Kani Roll</span>seasoned ground crab meat (8pcs) <span class="price">5.49</span> (12pcs) <span class="price">7.49</span></div>
      <div class="item"><span class="item-name">Vegetarian Roll</span>avocado, cucumber &amp; oshinko (8pcs) <span class="price">4.99</span> Add Ajitsuke egg <span class="price">0.99</span></div>
    </section>
  </main>

  <aside class="cover">
    <div class="cover-inner"></div>
    <div class="cover-calligraphy" role="img" aria-label="Large brush calligraphy character in warm brown"></div>
    <div class="cover-photo" role="img" aria-label="Close-up photo of a salmon and avocado sushi roll topped with roe"></div>
  </aside>
</body>
</html>
```